Business Card Design

We need a business card designed for a new company based in Melbourne called Kvt solutions. Kvt solutions provides management consulting specialising in the health and social services sector.

Kvt solutions offer a unique set of specialist skills │dealing with all levels of government │ unique communication skills│intimate knowledge of the health sector │solutions tailored to unique circumstances.

Kvt solutions takes on a select number of clients at any one time, this ensures that your organisation receives the attention required. On larger projects, Kvt solutions join up with other consultants to bring specialist skills to a project.
Updates

This is the first time I have used Pixel Harbor and thank you all for responding. The variation is amazing and makes it hard to decide. I have to ask some of my friends to give me their views. The response is fantastic. The one I pick will basically be the most visually appealing

Industry/Entity Type

Management Consulting

Contact Information for Business Card

Martin Oakes, Principal, Kvt solutions, 14 Wexcombe Ave, Larkdale VIC 3189, 0417 382 914, martino@kvtsolutions-example.com.au, www.kvtsolutions-example.com.au

```html
<!DOCTYPE html>
<html lang="en">
<head>
<meta charset="utf-8">
<title>Kvt solutions – Business Card</title>
<link rel="stylesheet" href="https://fonts.googleapis.com/css2?family=Open+Sans:wght@400&display=swap">
<style>
  :root {
    --page-bg: #e6e4e1;
    --brand-red: #c4162e;
    --brand-red-deep: #b01228;
    --charcoal: #2b2b2c;
    --ink-light: #ffffff;
    --card-shadow: rgba(0, 0, 0, 0.25);
  }
  * { box-sizing: border-box; margin: 0; padding: 0; }
  html, body {
    width: 1200px;
    height: 914px;
    overflow: hidden;
    background: var(--page-bg);
  }
  .stage {
    width: 1200px;
    height: 914px;
    display: flex;
    align-items: center;
    justify-content: center;
  }
  .business-card {
    position: relative;
    width: 900px;
    height: 514px;
    background: var(--charcoal);
    box-shadow: 0 10px 30px var(--card-shadow);
    overflow: hidden;
    font-family: "Open Sans", Arial, sans-serif;
    color: var(--ink-light);
  }
  .brand-band {
    position: absolute;
    left: 0;
    top: 0;
    width: 100%;
    height: 246px;
    background: var(--brand-red);
  }
  .brand-name {
    position: absolute;
    left: 0;
    top: 66px;
    width: 100%;
    text-align: center;
    font-size: 64px;
    font-weight: 400;
    letter-spacing: 2px;
    line-height: 1;
    color: var(--ink-light);
  }
  .pattern-strip {
    position: absolute;
    left: 0;
    top: 206px;
    width: 100%;
    height: 34px;
    display: block;
  }
  .contact-block {
    position: absolute;
    left: 0;
    top: 280px;
    width: 100%;
    text-align: center;
  }
  .person-name {
    font-size: 27px;
    letter-spacing: 0.5px;
    line-height: 1.2;
  }
  .person-role {
    font-size: 23px;
    line-height: 1.3;
    margin-bottom: 12px;
  }
  .contact-line {
    font-size: 19px;
    line-height: 1.4;
  }
</style>
</head>
<body>
  <main class="stage">
    <article class="business-card">
      <div class="brand-band">
        <div class="brand-name">Kvt solutions</div>
      </div>
      <svg class="pattern-strip" viewBox="0 0 900 34" preserveAspectRatio="none" role="img" aria-label="Decorative row of small cross marks along the base of the red band">
        <rect x="0" y="0" width="900" height="34" fill="var(--brand-red-deep)"/>
      </svg>
      <section class="contact-block">
        <p class="person-name">MARTIN OAKES</p>
        <p class="person-role">Principal</p>
        <p class="contact-line">Kvt solutions, 14 Wexcombe Ave,</p>
        <p class="contact-line">Larkdale VIC 3189, 0417 382 914,</p>
        <p class="contact-line">martino@kvtsolutions-example.com.au , www.kvtsolutions-example.com.au</p>
      </section>
    </article>
  </main>
</body>
</html>
```